Upscale business cards needed for Board of Directors

We need professional business cards created for members of our family business Board of Directors. We would like these relatively simple and straightforward, but also with a unique element to set them apart. Probably stick with neutral and simple colors - white, grey etc. We need space for the traditional elements, including name, title, address, email/phone number. And we will be creating several from this template so it needs to be template that is easy to switch information in and out of.
Business
See description

```html
<!DOCTYPE html>
<html lang="en">
<head>
<meta charset="utf-8">
<title>Kestrel Holdings – Business Card</title>
<link href="https://fonts.googleapis.com/css2?family=Lato:wght@300;400;900&display=swap" rel="stylesheet">
<style>
  :root {
    --gold: #b09c70;
    --ink: #111111;
    --paper: #ffffff;
    --rule: #8a8a8a;
    --backdrop: #e4e4e2;
  }
  * { box-sizing: border-box; margin: 0; padding: 0; }
  html, body { width: 1200px; height: 900px; overflow: hidden; }
  body {
    background: var(--backdrop);
    font-family: "Lato", sans-serif;
    position: relative;
  }
  .card {
    position: absolute;
    left: 280px;
    width: 640px;
    height: 366px;
    box-shadow: 0 10px 28px rgba(0,0,0,0.18);
    overflow: hidden;
  }
  .card--back { top: 66px; background: var(--gold); color: var(--paper); }
  .card--front { top: 468px; background: var(--paper); color: var(--ink); }

  .brand {
    font-family: "Lato", sans-serif;
    font-weight: 900;
    text-transform: uppercase;
    line-height: 1;
    text-align: center;
  }
  .brand__name { display: block; font-size: 58px; letter-spacing: 1px; }
  .brand__sub { display: block; font-size: 24px; letter-spacing: 16px; margin-top: 6px; padding-left: 16px; }

  .card--back .brand { position: absolute; left: 0; right: 0; top: 110px; }
  .card--back .back-url {
    position: absolute; left: 0; right: 0; top: 262px;
    text-align: center; font-size: 17px; letter-spacing: 2.5px; font-weight: 400;
  }

  .card--front .brand { position: absolute; right: 40px; top: 60px; width: 330px; color: var(--ink); }
  .card--front .brand__name { font-size: 44px; }
  .card--front .brand__sub { font-size: 19px; letter-spacing: 13px; padding-left: 13px; }

  .holder {
    position: absolute; left: 40px; top: 62px;
    font-size: 24px; font-weight: 300; color: var(--gold);
  }
  .holder__title { color: var(--ink); font-size: 18px; font-weight: 400; }
  .holder__sep { color: var(--ink); font-weight: 300; margin: 0 4px; }
  .name-rule {
    position: absolute; left: 40px; top: 100px; width: 500px;
    border-top: 1px solid var(--rule);
  }
  .contact {
    position: absolute; left: 40px; top: 112px;
    list-style: none; font-size: 17px; line-height: 23px;
  }
  .contact li { display: flex; align-items: center; gap: 10px; }
  .contact svg { width: 12px; height: 12px; fill: var(--gold); flex: none; }

  .address {
    position: absolute; right: 40px; bottom: 40px;
    text-align: right; font-size: 22px; line-height: 27px; font-weight: 400;
  }
  .footer-band { position: absolute; left: 0; bottom: 0; width: 640px; height: 120px; }
</style>
</head>
<body>

  <section class="card card--back" aria-label="Card back">
    <div class="brand">
      <span class="brand__name">Kestrel</span>
      <span class="brand__sub">Holdings</span>
    </div>
    <p class="back-url">www.kestrelhold.com</p>
  </section>

  <section class="card card--front" aria-label="Card front">
    <svg class="footer-band" viewBox="0 0 640 120" aria-hidden="true">
      <polygon points="0,48 300,48 310,60 300,72 0,72" fill="var(--ink)"/>
      <polygon points="0,72 300,72 310,60 330,120 0,120" fill="var(--gold)"/>
      <rect x="0" y="110" width="640" height="10" fill="var(--gold)"/>
    </svg>

    <p class="holder">Daniel Harper<span class="holder__sep">|</span><span class="holder__title">Director</span></p>
    <div class="name-rule"></div>

    <ul class="contact">
      <li>
        <svg viewBox="0 0 12 12"><path d="M2.5 0.5l2 2.5-1.2 1.4c.8 1.6 2 2.8 3.6 3.6l1.4-1.2 2.5 2-1.3 2.3C4.8 11 1 7.2.2 1.8z"/></svg>
        512 555 0140
      </li>
      <li>
        <svg viewBox="0 0 12 12"><rect x="3" y="0.5" width="6" height="3.5"/><rect x="0.5" y="4.5" width="11" height="5" rx="1"/><rect x="3" y="8" width="6" height="3.5"/></svg>
        512 555 0141
      </li>
      <li>
        <svg viewBox="0 0 12 12"><path d="M0.5 2h11v8h-11z M1 2.5l5 4 5-4" stroke="#fff" stroke-width="0.8"/></svg>
        info@kestrelhold.com
      </li>
      <li>
        <svg viewBox="0 0 12 12"><circle cx="6" cy="6" r="5.5"/><path d="M0.5 6h11M6 .5c-2.5 3-2.5 8 0 11M6 .5c2.5 3 2.5 8 0 11" stroke="#fff" stroke-width="0.7" fill="none"/></svg>
        www.kestrelhold.com
      </li>
    </ul>

    <div class="brand">
      <span class="brand__name">Kestrel</span>
      <span class="brand__sub">Holdings</span>
    </div>

    <address class="address" style="font-style: normal;">1450 Ridge Lane<br>Cedar TX 78010</address>
  </section>

</body>
</html>
```